Local Roofing/Construction company business needs new biz card design

We need a new business card design, current cards are from the start of this operation and generic at best. We are a local Construction Company (General Contractor) with a majority of our work originating from insurance claims-exterior finish work is the main focus (Roofs-Siding-Gutters etc). Heavily involved with homeowners and the low ball offers they receive from insurance company's after a insurable event takes place. I have attached some of our original logo file(s) below.

```html
<!DOCTYPE html>
<html lang="en">
<head>
<meta charset="utf-8">
<title>Ridgeline Builders – Business Card</title>
<link rel="stylesheet" href="https://fonts.googleapis.com/css2?family=Poppins:wght@400;600;700&display=swap">
<style>
  :root {
    --page-bg: #d9d6d4;
    --card-light: #efe7e6;
    --card-light-edge: #e2d6d5;
    --card-dark: #0d1f22;
    --accent-green: #2ed47a;
    --text-light: #ffffff;
    --text-dark: #0d1f22;
  }
  * { box-sizing: border-box; margin: 0; padding: 0; }
  html, body {
    width: 1200px;
    height: 900px;
    overflow: hidden;
    background: var(--page-bg);
    font-family: "Poppins", sans-serif;
  }
  .business-card {
    position: absolute;
    left: 100px;
    top: 141px;
    width: 1000px;
    height: 618px;
    overflow: hidden;
    background: linear-gradient(135deg, var(--card-light) 0%, var(--card-light-edge) 100%);
    box-shadow: 0 18px 40px rgba(0, 0, 0, 0.18);
  }
  .card-shapes {
    position: absolute;
    inset: 0;
  }
  .brand {
    position: absolute;
    left: 45px;
    top: 146px;
    display: flex;
    align-items: center;
    gap: 12px;
  }
  .brand-square {
    width: 30px;
    height: 30px;
    background: var(--accent-green);
  }
  .brand-name {
    font-weight: 700;
    font-size: 30px;
    letter-spacing: 0.5px;
    color: var(--text-dark);
    line-height: 1;
  }
  .card-details {
    position: absolute;
    left: 545px;
    top: 117px;
    color: var(--text-light);
  }
  .person-name {
    font-weight: 600;
    font-size: 37px;
    line-height: 1.1;
    color: var(--accent-green);
    letter-spacing: 0.5px;
  }
  .person-title {
    font-weight: 400;
    font-size: 27px;
    line-height: 1.2;
  }
  .address {
    margin-top: 40px;
    font-size: 27px;
    line-height: 36px;
    font-style: normal;
  }
  .contact-list {
    list-style: none;
    margin-top: 44px;
    font-size: 27px;
    line-height: 36px;
  }
  .contact-list li {
    display: flex;
    align-items: center;
    gap: 9px;
  }
  .contact-icon {
    width: 26px;
    height: 26px;
    flex: none;
  }
</style>
</head>
<body>
  <div class="business-card">
    <svg class="card-shapes" width="1000" height="618" viewBox="0 0 1000 618" aria-hidden="true">
      <path fill="var(--accent-green)" d="M440,0 C485,60 495,150 465,270 C435,380 425,450 432,520 C437,570 450,600 460,618 L1000,618 L1000,0 Z"/>
      <path fill="var(--card-dark)" d="M490,0 C520,70 515,160 490,270 C462,380 440,450 442,520 C445,570 455,600 468,618 L1000,618 L1000,0 Z"/>
    </svg>

    <div class="brand">
      <span class="brand-square"></span>
      <span class="brand-name">RIDGELINE BUILDERS</span>
    </div>

    <div class="card-details">
      <h1 class="person-name">DANIEL MARSH</h1>
      <p class="person-title">Managing Director</p>

      <address class="address">
        421, Address line<br>
        goes here<br>
        45452,Country Name
      </address>

      <ul class="contact-list">
        <li>
          <svg class="contact-icon" viewBox="0 0 24 24" aria-hidden="true">
            <path fill="var(--accent-green)" d="M6.6 10.8a15.1 15.1 0 0 0 6.6 6.6l2.2-2.2a1 1 0 0 1 1-.25 11.4 11.4 0 0 0 3.6.57 1 1 0 0 1 1 1V20a1 1 0 0 1-1 1A17 17 0 0 1 3 4a1 1 0 0 1 1-1h3.5a1 1 0 0 1 1 1c0 1.25.2 2.45.57 3.6a1 1 0 0 1-.25 1z"/>
          </svg>
          044-555 018 272
        </li>
        <li>
          <svg class="contact-icon" viewBox="0 0 24 24" aria-hidden="true">
            <rect x="2" y="5" width="20" height="14" fill="var(--accent-green)"/>
            <path d="M2 5l10 8 10-8" fill="none" stroke="var(--card-dark)" stroke-width="1.6"/>
          </svg>
          info@ridgelinebuild.com
        </li>
        <li>
          <svg class="contact-icon" viewBox="0 0 24 24" aria-hidden="true">
            <g fill="none" stroke="var(--accent-green)" stroke-width="2">
              <circle cx="12" cy="12" r="9.5"/>
              <ellipse cx="12" cy="12" rx="4.2" ry="9.5"/>
              <line x1="2.5" y1="12" x2="21.5" y2="12"/>
              <line x1="4" y1="7" x2="20" y2="7"/>
              <line x1="4" y1="17" x2="20" y2="17"/>
            </g>
          </svg>
          www.ridgelinebuild.com
        </li>
      </ul>
    </div>
  </div>
</body>
</html>
```